Breakfast Cafe - The Sunny Nook

It is for my breakfast and lunch cafe with a hawaiian / beach theme. I am Open every day from 6am to 3pm. We serve traditional American food such as omelettes, pancakes, burgers and sandwiches. I'll upload my old card and my new logo to be used. We have a lot of day to day regulars who eat there during the week, our t-shirts actually say 'Locals Only' on them. Hope this helps. Thanks.

Target Market(s)

anyone who has an appetite!

Industry/Entity Type

American Restaurant

Contact Information for Business Card

4815C Marlow Grove Avenue
Harbor Cove, California
(555) 731-2294

Requirements
Must have
• Address and phone number easily readable.
Nice to have
• beach or tropical theme

```html
<!DOCTYPE html>
<html lang="en">
<head>
<meta charset="utf-8">
<title>The Sunny Nook – Business Card</title>
<link href="https://fonts.googleapis.com/css2?family=Oswald:wght@500;600&family=Great+Vibes&display=swap" rel="stylesheet">
<style>
  :root {
    --page-bg: #d8d5d0;
    --card-bg: #eceeed;
    --card-edge: #c9cccb;
    --brown: #8a3f1c;
    --teal: #2f9aa6;
    --orange: #e98a2a;
    --ink: #1c1c1c;
    --cream: #fbefe3;
    --cafe-brown: #7a2f12;
    --red: #9c1420;
  }
  html, body {
    margin: 0;
    width: 1200px;
    height: 969px;
    overflow: hidden;
    background: var(--page-bg);
  }
  .card {
    position: absolute;
    left: 100px;
    top: 200px;
    width: 1000px;
    height: 570px;
    border-radius: 26px;
    overflow: hidden;
    background: linear-gradient(160deg, #f4f5f4 0%, var(--card-bg) 55%, #e2e5e4 100%);
    box-shadow: 0 0 0 2px var(--card-edge), 0 18px 40px rgba(0,0,0,.18);
    font-family: "Oswald", "Arial Narrow", sans-serif;
  }
  .card-wave { position: absolute; inset: 0; }
  .contact {
    position: absolute;
    left: 60px;
    top: 50px;
    color: var(--cream);
    text-transform: uppercase;
    font-weight: 500;
    line-height: 1.3;
    white-space: nowrap;
  }
  .contact .street, .contact .city { font-size: 33px; letter-spacing: .5px; }
  .contact .phone { font-size: 38px; margin-top: 4px; }
  .motto {
    position: absolute;
    left: 50px;
    top: 232px;
    font-family: "Great Vibes", cursive;
    font-size: 58px;
    color: var(--cream);
    transform: rotate(-4deg);
    white-space: nowrap;
  }
  .brand {
    position: absolute;
    left: 570px;
    top: 62px;
    width: 380px;
    text-align: center;
  }
  .brand-dot {
    display: block;
    margin: 0 auto 20px;
    width: 170px;
    height: 170px;
    border-radius: 50%;
    background: var(--teal);
  }
  .brand-name {
    font-size: 44px;
    font-weight: 600;
    color: var(--teal);
    text-transform: uppercase;
    letter-spacing: 1px;
    white-space: nowrap;
  }
  .services {
    position: absolute;
    right: 62px;
    top: 400px;
    text-align: right;
    text-transform: uppercase;
    font-weight: 500;
    line-height: 1.25;
    white-space: nowrap;
  }
  .services .kind { font-size: 31px; color: var(--cafe-brown); }
  .services .hours { font-size: 25px; color: var(--teal); }
  .services .menu { font-size: 22px; color: var(--red); margin-top: 4px; }
</style>
</head>
<body>
  <div class="card">
    <svg class="card-wave" viewBox="0 0 1000 570" aria-hidden="true">
      <path d="M0,0 H770 C610,50 570,210 440,330 C330,430 160,480 0,500 Z" fill="var(--orange)"/>
      <path d="M0,0 H745 C590,45 550,200 425,318 C320,415 155,462 0,482 Z" fill="var(--teal)"/>
      <path d="M0,0 H722 C572,42 532,192 412,306 C310,402 150,448 0,468 Z" fill="var(--ink)"/>
      <path d="M0,0 H715 C566,42 526,190 408,302 C306,398 148,444 0,464 Z" fill="var(--brown)"/>
    </svg>

    <div class="contact">
      <div class="street">4815C Marlow Grove Avenue</div>
      <div class="city">Harbor Cove, California</div>
      <div class="phone">P.(555) 731-2294</div>
    </div>

    <div class="motto">Locals Only</div>

    <div class="brand">
      <span class="brand-dot"></span>
      <div class="brand-name">The Sunny Nook</div>
    </div>

    <div class="services">
      <div class="kind">Breakfast &amp; Lunch Cafe</div>
      <div class="hours">Open every day from 6am to 3pm.</div>
      <div class="menu">Serving classic diner favorites</div>
    </div>
  </div>
</body>
</html>
```